Business Card Design

Business Card for professional consulting firm working with large financial institutions.

Target Market(s)

Executive buyers

Industry/Entity Type

Banking

Contact Information for Business Card

Mild creativity wanted. Not boring, but do elaborate artwork.

Font styles to use
Serif
Sans Serif

Colors

Designer to choose colors to be used in the design.

Requirements
Must have
• Standard business card features - company name, individual name, telephone, website, email, locations.
Nice to have
• Two colors
Should not have
• too many colors, fancy printing, cartoons.

```html
<!DOCTYPE html>
<html lang="en">
<head>
<meta charset="utf-8">
<title>Harlow Advisory – Business Card</title>
<link href="https://fonts.googleapis.com/css2?family=Roboto:wght@400&family=Roboto+Slab:wght@400;700&family=Source+Serif+4:wght@400&display=swap" rel="stylesheet">
<style>
  :root {
    --backdrop: #e4e4e4;
    --paper: #f3f3f3;
    --ink: #000000;
    --band-grey: #a6a6a6;
    --back-grey: #a9a9a9;
    --on-dark: #ffffff;
    --rule: #9a9a9a;
    --back-url: #4a4a4a;
  }
  html, body {
    margin: 0;
    padding: 0;
    width: 1200px;
    height: 960px;
    overflow: hidden;
    background: var(--backdrop);
  }
  .stage {
    position: relative;
    width: 1200px;
    height: 960px;
  }
  .card {
    position: absolute;
    width: 600px;
    height: 343px;
    overflow: hidden;
    box-shadow: 0 2px 4px rgba(0,0,0,0.35);
  }
  .card--front { left: 314px; top: 113px; background: var(--paper); }
  .card--back  { left: 311px; top: 472px; background: var(--back-grey); }

  .card__shapes { position: absolute; inset: 0; }

  .wordmark {
    position: absolute;
    font-family: "Source Serif 4", Georgia, serif;
    font-weight: 400;
    color: var(--ink);
    margin: 0;
    line-height: 1;
    letter-spacing: 0.2px;
  }
  .card--front .wordmark { left: 70px; top: 62px; font-size: 28px; }
  .card--back .wordmark { left: 0; right: 0; top: 150px; text-align: center; font-size: 33px; }

  .holder {
    position: absolute;
    right: 32px;
    top: 202px;
    text-align: right;
    color: var(--on-dark);
    font-family: "Roboto Slab", Georgia, serif;
  }
  .holder__name { margin: 0; font-size: 20px; font-weight: 700; letter-spacing: 0.5px; line-height: 24px; }
  .holder__title { margin: 1px 0 0; font-size: 14px; font-weight: 400; line-height: 16px; }

  .contact {
    position: absolute;
    left: 36px;
    top: 260px;
    margin: 0;
    padding: 0;
    list-style: none;
    font-family: "Roboto", Arial, sans-serif;
    font-size: 14px;
    color: var(--on-dark);
  }
  .contact__item { display: flex; align-items: center; height: 19px; }
  .contact__icon { width: 13px; height: 13px; margin-right: 7px; fill: var(--on-dark); }

  .contact-rule {
    position: absolute;
    left: 153px;
    right: 34px;
    top: 270px;
    height: 1px;
    background: var(--rule);
  }

  .address {
    position: absolute;
    right: 32px;
    top: 280px;
    margin: 0;
    text-align: right;
    font-family: "Roboto", Arial, sans-serif;
    font-style: normal;
    font-size: 14px;
    line-height: 19px;
    color: var(--on-dark);
  }

  .back-url {
    position: absolute;
    left: 0; right: 0;
    top: 280px;
    margin: 0;
    line-height: 18px;
    text-align: center;
    font-family: "Roboto", Arial, sans-serif;
    font-size: 14px;
    letter-spacing: 5px;
    color: var(--back-url);
  }
</style>
</head>
<body>
<main class="stage">

  <section class="card card--front" aria-label="Business card front">
    <svg class="card__shapes" width="600" height="343" viewBox="0 0 600 343" aria-hidden="true">
      <polygon class="accent-band" points="0,206 320,206 309,220 0,220" fill="var(--band-grey)"/>
      <polygon class="contact-panel" points="0,222 310,222 346,176 600,176 600,343 0,343" fill="var(--ink)"/>
    </svg>

    <p class="wordmark">Harlow Advisory</p>

    <div class="holder">
      <p class="holder__name">DANIEL WHITFORD</p>
      <p class="holder__title">CEO/FOUNDER</p>
    </div>

    <div class="contact-rule"></div>

    <ul class="contact">
      <li class="contact__item">
        <svg class="contact__icon" viewBox="0 0 16 16" aria-hidden="true"><path d="M3.5 1.5l2.5 0 1.2 3.2-1.6 1.3c.8 1.8 2.2 3.2 4 4l1.3-1.6 3.2 1.2 0 2.5c0 .8-.7 1.4-1.5 1.4C6.6 13.2 2.8 9.4 2.1 3c0-.8.6-1.5 1.4-1.5z"/></svg>
        555 210 4476
      </li>
      <li class="contact__item">
        <svg class="contact__icon" viewBox="0 0 16 16" aria-hidden="true"><path d="M1 3h14v1.2L8 8.6 1 4.2z M1 5.6l7 4.4 7-4.4V13H1z"/></svg>
        info@harlowadvisory.com
      </li>
      <li class="contact__item">
        <svg class="contact__icon" viewBox="0 0 16 16" aria-hidden="true"><circle cx="8" cy="8" r="7"/><path d="M1.5 8h13M8 1c2 2 2 12 0 14M8 1c-2 2-2 12 0 14" stroke="var(--ink)" stroke-width="1.1" fill="none"/></svg>
        www.harlowadvisory.com
      </li>
    </ul>

    <address class="address">
      2140 Birchwood Lane<br>
      Fairbanks, Alaska 99701
    </address>
  </section>

  <section class="card card--back" aria-label="Business card back">
    <p class="wordmark">Harlow Advisory</p>
    <p class="back-url">www.harlowadvisory.com</p>
  </section>

</main>
</body>
</html>
```